Law firm business card

Information:

Me Mireille Dufontaine

website: dufontaine-legal.ca
email: mireille@dufontaine-legal.ca
Phone: 514 382-5167
Fax: 514 382-5169

Address:
Dufontaine and associates
2719 Belcourtier
Montreal, QC
H2K 3M9

Areas of Expertise:
Franchise Agreements, Financing, Acquisition, Real Estate Development, Commercial Agreements and Corporate Law

Target Market(s)

executives, companie managers

Industry/Entity Type

Business

Colors
f78f20
000000

Requirements
Must have
• Must use the logo, the logo is available here:

https://www.filecrate-example.com/sh/qyt3kwud82mfa0x/BBQTn7Lhvpe_kRTXwJM_GhcYb

```html
<!DOCTYPE html>
<html lang="en">
<head>
<meta charset="utf-8">
<title>Dufontaine &amp; Associates — Business Card</title>
<link rel="stylesheet" href="https://fonts.googleapis.com/css2?family=Cinzel:wght@500&family=Oswald:wght@500&family=Open+Sans:wght@400;600&display=swap">
<style>
  :root {
    --orange: #f78f20;
    --ink: #000000;
    --slate: #4a4b4f;
    --paper: #ffffff;
    --backdrop: #e9e6e1;
  }
  * { box-sizing: border-box; margin: 0; padding: 0; }
  html, body {
    width: 1076px; height: 1200px; overflow: hidden;
    background: var(--backdrop);
    font-family: "Open Sans", Arial, sans-serif;
  }
  .sheet { position: relative; width: 1076px; height: 1200px; }
  .card {
    position: absolute; left: 108px; width: 860px; height: 490px;
    background: var(--paper); overflow: hidden;
    box-shadow: 0 10px 28px rgba(0,0,0,.18);
  }
  .card--front { top: 80px; }
  .card--back  { top: 630px; }
  .card__art { position: absolute; inset: 0; }

  .brand { position: absolute; display: flex; align-items: center; gap: 22px; }
  .brand__dot {
    width: 74px; height: 74px; border-radius: 50%;
    border: 3px solid var(--orange); flex: none;
  }
  .brand__name {
    font-family: "Cinzel", Georgia, serif; font-weight: 500;
    color: var(--orange); line-height: 1.05; letter-spacing: 1px;
    white-space: nowrap;
  }
  .card--front .brand { left: 230px; top: 205px; }
  .card--front .brand__name { font-size: 40px; }
  .card--front .brand__name small { display: block; font-size: 24px; letter-spacing: 3px; }

  .card--back .brand { left: 60px; top: 110px; gap: 16px; }
  .card--back .brand__dot { width: 54px; height: 54px; }
  .card--back .brand__name { font-size: 28px; }
  .card--back .brand__name small { display: block; font-size: 17px; letter-spacing: 2px; }

  .address {
    position: absolute; left: 60px; bottom: 52px;
    display: flex; gap: 12px; align-items: flex-start;
    font-size: 15px; color: var(--slate); line-height: 1.5;
  }
  .icon {
    width: 22px; height: 22px; flex: none; background: var(--slate);
    display: grid; place-items: center;
  }
  .icon svg { width: 14px; height: 14px; fill: var(--paper); }

  .contacts {
    position: absolute; right: 48px; top: 58px;
    list-style: none; text-align: right;
  }
  .contacts li {
    display: flex; justify-content: flex-end; align-items: center; gap: 12px;
    font-size: 15px; color: var(--ink); margin-bottom: 14px;
    white-space: nowrap;
  }
  .holder {
    position: absolute; right: 48px; bottom: 62px;
    display: flex; align-items: center; gap: 14px; text-align: right;
  }
  .holder__name {
    font-family: "Oswald", Arial, sans-serif; font-weight: 500;
    font-size: 26px; color: var(--slate); letter-spacing: 1px; line-height: 1;
    white-space: nowrap;
  }
  .holder__title {
    font-size: 11px; font-weight: 600; letter-spacing: 2px; color: var(--ink); margin-top: 6px;
    white-space: nowrap;
  }
  .holder__rule { width: 4px; height: 48px; background: var(--slate); }
</style>
</head>
<body>
<main class="sheet">

  <section class="card card--front" aria-label="Card front">
    <svg class="card__art" viewBox="0 0 860 490" aria-hidden="true">
      <polygon points="0,0 52,0 52,250 0,300" fill="var(--slate)"/>
      <polygon points="0,0 40,0 40,250 0,290" fill="var(--orange)"/>
      <polygon points="860,490 808,490 808,240 860,190" fill="var(--slate)"/>
      <polygon points="860,490 820,490 820,240 860,200" fill="var(--orange)"/>
    </svg>
    <div class="brand">
      <span class="brand__dot"></span>
      <p class="brand__name">Dufontaine<small>&amp; Associates</small></p>
    </div>
  </section>

  <section class="card card--back" aria-label="Card back">
    <svg class="card__art" viewBox="0 0 860 490" aria-hidden="true">
      <polygon points="410,0 860,0 860,490 560,490" fill="var(--orange)"/>
      <polygon points="430,235 446,235 530,490 514,490" fill="var(--slate)"/>
      <polygon points="398,270 414,270 486,490 470,490" fill="var(--slate)"/>
    </svg>

    <div class="brand">
      <span class="brand__dot"></span>
      <p class="brand__name">Dufontaine<small>&amp; Associates</small></p>
    </div>

    <div class="address">
      <span class="icon"><svg viewBox="0 0 24 24"><path d="M12 2a7 7 0 0 0-7 7c0 5 7 13 7 13s7-8 7-13a7 7 0 0 0-7-7zm0 9.5A2.5 2.5 0 1 1 12 6.5a2.5 2.5 0 0 1 0 5z"/></svg></span>
      <p>2719 Belcourtier<br>Montreal, QC H2K 3M9</p>
    </div>

    <ul class="contacts">
      <li>514 382-5167<span class="icon"><svg viewBox="0 0 24 24"><path d="M6.6 10.8a15 15 0 0 0 6.6 6.6l2.2-2.2c.3-.3.7-.4 1-.2 1.1.4 2.3.6 3.6.6.6 0 1 .4 1 1V20c0 .6-.4 1-1 1A17 17 0 0 1 3 4c0-.6.4-1 1-1h3.5c.6 0 1 .4 1 1 0 1.300.2 2.500.6 3.600.1.300 0 .700-.2 1z"/></svg></span></li>
      <li>514 382-5169<span class="icon"><svg viewBox="0 0 24 24"><path d="M6 3h12v5H6zM4 9h16a2 2 0 0 1 2 2v6h-4v4H6v-4H2v-6a2 2 0 0 1 2-2zm4 7v3h8v-3z"/></svg></span></li>
      <li>mireille@dufontaine-legal.ca<span class="icon"><svg viewBox="0 0 24 24"><path d="M3 5h18v14H3zm2 2v.5l7 4.5 7-4.5V7z"/></svg></span></li>
      <li>www.dufontaine-legal.ca<span class="icon"><svg viewBox="0 0 24 24"><path d="M12 2a10 10 0 1 0 0 20 10 10 0 0 0 0-20zm6.9 9h-3a15 15 0 0 0-1.3-5.6A8 8 0 0 1 18.9 11zM12 4c.9 1.2 1.8 3.8 1.9 7h-3.8c.1-3.2 1-5.8 1.9-7zM9.4 5.4A15 15 0 0 0 8.1 11h-3a8 8 0 0 1 4.3-5.6zM5.1 13h3a15 15 0 0 0 1.3 5.6A8 8 0 0 1 5.1 13zm6.9 7c-.9-1.2-1.8-3.8-1.9-7h3.8c-.1 3.2-1 5.8-1.9 7zm2.6-1.4a15 15 0 0 0 1.3-5.6h3a8 8 0 0 1-4.3 5.6z"/></svg></span></li>
    </ul>

    <div class="holder">
      <div>
        <p class="holder__name">MIREILLE DUFONTAINE</p>
        <p class="holder__title">GENERAL MANAGER</p>
      </div>
      <span class="holder__rule"></span>
    </div>
  </section>

</main>
</body>
</html>
```